Book Cover: Quiet Harbor: Small Ceremonies For The Restless Soul

I would like a full cover spread- front, back and spine as well as a stand alone front cover for Kindle for the book. Design a cover that mirrors the profound depth and dynamic energy of 'Quiet Harbor.' Envision a visual tapestry that draws readers into a transformative journey, where spirituality and self-care unite. Explore vibrant colors, intricate textures, and a sense of inner radiance that beckons readers to explore the book's rich wisdom within. See images for design inspiration attached. Even though some of the images are cartoon, I'd like the cover to be more serious than playful and very elegant.

About this book (back cover copy)
Are you ready to embark on a transformative journey and elevate your daily existence? "Quiet Harbor" is a treasure trove of practical yet profound rituals and wisdom from renowned self-care, healing, and spirituality experts.

Within these pages, you'll uncover a tapestry of guidance and insight from some of the world's most respected mentors. Their collective wisdom is your key to creating a sacred sanctuary within your everyday life.

From invigorating morning rituals to meditative practices, empowering affirmations, and transformative energy healing, you'll find a rich tapestry of tools to nurture a deeper connection with yourself and the universe.

Whether you're a seasoned practitioner or a newcomer to the world of self-care and spirituality, "Quiet Harbor" is your trusted companion on the journey to transform your life and elevate your daily experience. Open this book today and start your sacred, fulfilling adventure.

Colors
0094D4
00A9DD
6FCCEA
C7EBF8
E9F6FB
E54698
E96AAD
F1A4CE
F9D9EA
FCEFF6
6B429C
8869AF
B7A5CE
E3DAEB
F3F0F8

Requirements
Must have
• Title: Quiet Harbor: Subtitle: Small Ceremonies For The Restless Soul Name of Publisher: Lantern Bough Publishing- Logo on the back Back cover copy

```html
<!DOCTYPE html>
<html lang="en">
<head>
<meta charset="utf-8">
<title>Quiet Harbor — Cover Spread</title>
<link rel="stylesheet" href="https://fonts.googleapis.com/css2?family=Mr+Dafoe&family=Cormorant+Garamond:ital,wght@0,500;0,600;1,400&family=Crimson+Text:ital,wght@0,400;0,700;1,400&family=Questrial&family=Roboto:wght@400;700&display=swap">
<style>
  :root {
    --stage: #222222;
    --paper: #ffffff;
    --ink: #111111;
    --grey-text: #808080;
    --spine-teal: #2f5f66;
    --gold-light: #f9e27a;
    --gold-mid: #d9b24a;
    --gold-deep: #a97d22;
    --leaf-teal: #3f8f8e;
    --leaf-pale: #c9e3e3;
    --petal: #f4a9bd;
    --petal-pale: #fbdde6;
    --barcode-box: #efefef;
  }
  * { box-sizing: border-box; margin: 0; padding: 0; }
  html, body { width: 1200px; height: 1200px; overflow: hidden; background: var(--stage); }

  .spread {
    position: absolute; left: 32px; top: 197px;
    width: 1135px; height: 805px;
    background: var(--paper); overflow: hidden;
  }

  .art { position: absolute; filter: blur(6px); }
  .art--front-bouquet {
    left: 700px; top: -20px; width: 460px; height: 620px;
    background:
      radial-gradient(ellipse 80px 70px at 72% 12%, var(--petal) 0%, var(--petal-pale) 55%, transparent 75%),
      radial-gradient(ellipse 90px 80px at 86% 38%, var(--petal) 0%, var(--petal-pale) 55%, transparent 75%),
      radial-gradient(ellipse 170px 90px at 45% 20%, var(--leaf-teal) 0%, rgba(63,143,142,.5) 45%, transparent 75%),
      radial-gradient(ellipse 110px 150px at 70% 65%, var(--leaf-teal) 0%, rgba(63,143,142,.45) 50%, transparent 78%),
      radial-gradient(ellipse 200px 160px at 25% 45%, var(--leaf-pale) 0%, transparent 75%);
  }
  .art--front-sprigs {
    left: 880px; top: 520px; width: 260px; height: 300px;
    background: radial-gradient(ellipse 120px 150px at 60% 55%, rgba(201,227,227,.8) 0%, transparent 75%);
  }
  .art--front-base {
    left: 600px; top: 650px; width: 360px; height: 170px;
    background: radial-gradient(ellipse 180px 80px at 40% 80%, rgba(201,227,227,.7) 0%, transparent 75%);
  }
  .art--back-blossom {
    left: -40px; top: 20px; width: 200px; height: 200px;
    background: radial-gradient(circle at 40% 50%, var(--petal-pale) 0%, rgba(251,221,230,.6) 45%, transparent 72%);
  }
  .art--back-top-leaves {
    left: 100px; top: -30px; width: 440px; height: 170px;
    background:
      radial-gradient(ellipse 180px 70px at 40% 40%, rgba(201,227,227,.8) 0%, transparent 75%),
      radial-gradient(ellipse 40px 30px at 85% 60%, var(--petal-pale) 0%, transparent 75%);
  }
  .art--back-foliage {
    left: -30px; top: 390px; width: 260px; height: 440px;
    background:
      radial-gradient(ellipse 110px 140px at 45% 75%, var(--leaf-teal) 0%, rgba(63,143,142,.45) 50%, transparent 78%),
      radial-gradient(ellipse 70px 140px at 20% 30%, var(--leaf-pale) 0%, transparent 75%);
  }

  .gold {
    background: linear-gradient(100deg, var(--gold-light) 0%, var(--gold-mid) 45%, var(--gold-deep) 100%);
    -webkit-background-clip: text; background-clip: text; color: transparent;
  }
  .script {
    font-family: "Mr Dafoe", cursive; font-weight: 400;
    line-height: 1.3; white-space: nowrap;
  }
  .script-word { position: absolute; display: block; padding: 0 .25em; }

  /* back cover */
  .back-title__main { left: 140px; top: 38px; font-size: 96px; }
  .back-title__second { left: 190px; top: 112px; font-size: 60px; }
  .back-subtitle {
    position: absolute; left: 0; width: 546px; top: 193px; text-align: center;
    font-family: "Cormorant Garamond", serif; font-size: 22.5px; color: var(--grey-text); white-space: nowrap;
  }
  .back-subtitle em { font-style: italic; }
  .back-subtitle strong { font-weight: 600; }
  .blurb {
    position: absolute; left: 64px; width: 418px; top: 232px; text-align: center;
    font-family: "Crimson Text", serif; font-size: 13.8px; line-height: 18.7px; color: var(--ink);
  }
  .blurb p + p { margin-top: 18.7px; }
  .blurb b { font-weight: 700; }
  .publisher-mark {
    position: absolute; left: 172px; width: 160px; top: 694px; text-align: center;
    font-family: "Questrial", sans-serif; font-size: 19px; line-height: 27px; letter-spacing: 1px; color: var(--ink);
  }
  .barcode-area { position: absolute; left: 339px; top: 683px; width: 140px; height: 84px; background: var(--barcode-box); }

  /* spine */
  .spine {
    position: absolute; left: 546px; top: 0; width: 43px; height: 805px;
    writing-mode: vertical-rl; display: flex; align-items: center; padding-top: 22px;
  }
  .spine__title { font-size: 50px; line-height: 1.3; padding: 4px 0; margin-bottom: 4px; }
  .spine__subtitle { font-family: "Cormorant Garamond", serif; font-size: 17px; color: var(--grey-text); white-space: nowrap; }
  .spine__subtitle em { font-style: italic; }
  .spine__subtitle strong { font-weight: 600; }
  .spine__publisher { margin-top: 18px; font-family: "Roboto", sans-serif; font-size: 15px; color: var(--spine-teal); white-space: nowrap; }
  .spine__publisher b { font-weight: 700; }

  /* front cover */
  .front-title__main { left: 590px; top: 300px; font-size: 190px; }
  .front-title__second { left: 690px; top: 478px; font-size: 108px; }
  .front-subtitle {
    position: absolute; left: 630px; width: 390px; top: 640px; text-align: center;
    font-family: "Cormorant Garamond", serif; color: var(--grey-text);
  }
  .front-subtitle__lead { display: block; font-style: italic; font-size: 33px; line-height: 38px; }
  .front-subtitle__main { display: block; font-weight: 600; font-size: 35px; line-height: 39px; }
</style>
</head>
<body>
  <main class="spread">
    <div class="art art--back-blossom" role="img" aria-label="Soft watercolour pink blossom"></div>
    <div class="art art--back-top-leaves" role="img" aria-label="Faint watercolour leaves and pink petals"></div>
    <div class="art art--back-foliage" role="img" aria-label="Watercolour teal leaves and eucalyptus"></div>
    <div class="art art--front-bouquet" role="img" aria-label="Watercolour bouquet of pink blossoms with teal leaves"></div>
    <div class="art art--front-sprigs" role="img" aria-label="Faint watercolour eucalyptus sprigs"></div>
    <div class="art art--front-base" role="img" aria-label="Faint watercolour leaves"></div>

    <section class="back-cover">
      <h2 class="back-title script">
        <span class="script-word back-title__main gold">Quiet</span>
        <span class="script-word back-title__second gold">Harbor</span>
      </h2>
      <p class="back-subtitle"><em>Small Ceremonies for</em> <strong>The Restless Soul</strong></p>
      <div class="blurb">
        <p><b>Are you ready to embark on a transformative journey and elevate your daily existence?</b> <i>"Quiet Harbor"</i> is a treasure trove of practical yet profound rituals and wisdom from renowned self-care, healing, and spirituality experts.</p>
        <p>Within these pages, you'll uncover a tapestry of guidance and insight from some of the world's most respected mentors. Their collective wisdom is your key to creating a sacred sanctuary within your everyday life.</p>
        <p>From invigorating morning rituals to meditative practices, empowering affirmations, and transformative energy healing, you'll find a rich tapestry of tools to nurture a deeper connection with yourself and the universe.</p>
        <p>Whether you're a seasoned practitioner or a newcomer to the world of self-care and spirituality, "Quiet Harbor" is your trusted companion on the journey to transform your life and elevate your daily experience. Open this book today and start your sacred, fulfilling adventure.</p>
      </div>
      <p class="publisher-mark">Lantern Bough<br>Publishing</p>
      <div class="barcode-area"></div>
    </section>

    <section class="spine">
      <span class="spine__title script gold">Quiet Harbor</span>
      <span class="spine__subtitle"><em>Small Ceremonies for</em> <strong>The Restless Soul</strong></span>
      <span class="spine__publisher"><b>Lantern Bough</b> Publishing</span>
    </section>

    <section class="front-cover">
      <h1 class="front-title script">
        <span class="script-word front-title__main gold">Quiet</span>
        <span class="script-word front-title__second gold">Harbor</span>
      </h1>
      <p class="front-subtitle">
        <span class="front-subtitle__lead">Small Ceremonies for</span>
        <span class="front-subtitle__main">The Restless<br>Soul</span>
      </p>
    </section>
  </main>
</body>
</html>
```